Visitenkarten-Design für Boutique-Unternehmensberatung
Zielgruppe
Boutique Unternehmensberatung für die Chemische Industrie. Wir unterstützen Unternehmen, die Beziehung zu Ihren Händlern zu optimieren.
Vorläufige Website vertriebsbruecke-online.de kann ggf weitere Einblicke geben. Hinweis: Diese Website wurde bisher noch nicht professionell erstellt.
Aufgabenstellung
Die Visitenkarte sollte vertrauenserweckend und seriös wirken. Zeitgleich aber auch modern.

```html
<!DOCTYPE html>
<html lang="de">
<head>
<meta charset="utf-8">
<title>Visitenkarte – Vertriebsbrücke</title>
<link rel="stylesheet" href="https://fonts.googleapis.com/css2?family=Montserrat:wght@300;400;500;700&display=swap">
<style>
  :root {
    --brand-blue: #0f5592;
    --paper: #ffffff;
    --backdrop: #c4c6ca;
    --photo-light: #d9dde2;
    --photo-mid: #b08a78;
  }
  * { margin: 0; padding: 0; box-sizing: border-box; }
  html, body { width: 1200px; height: 852px; overflow: hidden; }
  body {
    background: var(--backdrop);
    font-family: "Montserrat", Arial, sans-serif;
    display: flex;
    align-items: center;
    justify-content: center;
    gap: 60px;
  }
  .card {
    position: relative;
    width: 500px;
    height: 324px;
    box-shadow: 0 6px 18px rgba(0,0,0,0.18);
    overflow: hidden;
  }

  /* Front */
  .card--front {
    background: var(--brand-blue);
    display: flex;
    align-items: center;
    justify-content: center;
  }
  .wordmark {
    display: flex;
    align-items: center;
    gap: 10px;
    font-weight: 500;
    white-space: nowrap;
  }
  .wordmark__dot {
    width: 14px; height: 14px;
    border-radius: 50%;
    background: currentColor;
    flex: none;
  }
  .card--front .wordmark { color: var(--paper); font-size: 30px; }

  /* Back */
  .card--back { background: var(--paper); color: var(--brand-blue); }
  .bar { position: absolute; background: var(--brand-blue); height: 5px; }
  .bar--top-right { top: 36px; left: 466px; right: 0; }
  .bar--personal { top: 122px; left: 28px; width: 352px; }
  .bar--bottom { top: 292px; left: 28px; right: 0; }

  .person { position: absolute; left: 28px; top: 44px; }
  .person__heading { display: flex; align-items: baseline; gap: 7px; white-space: nowrap; }
  .person__name { font-size: 22px; font-weight: 700; }
  .person__role { font-size: 12.5px; font-weight: 300; }
  .person__role::before { content: "•"; font-weight: 700; margin-right: 7px; }

  .contact-list { list-style: none; margin-top: 8px; }
  .contact-list li {
    display: flex; align-items: center; gap: 7px;
    font-size: 11px; font-weight: 400; line-height: 17px;
    white-space: nowrap;
  }
  .icon {
    width: 11px; height: 11px; flex: none;
    border-radius: 50%;
    background: var(--brand-blue);
    display: flex; align-items: center; justify-content: center;
  }
  .icon svg { width: 7px; height: 7px; }

  .portrait {
    position: absolute; left: 396px; top: 24px;
    width: 70px; height: 70px; border-radius: 50%;
    background: radial-gradient(circle at 45% 45%, var(--photo-mid), #c9b3a8 55%, var(--photo-light));
  }

  .card--back .wordmark {
    position: absolute; right: 22px; top: 150px;
    color: var(--brand-blue); font-size: 13px; font-weight: 700; gap: 6px;
  }
  .card--back .wordmark__dot { width: 9px; height: 9px; }

  .company { position: absolute; left: 60px; top: 150px; }
  .company__address { font-size: 11px; line-height: 16px; font-weight: 400; white-space: nowrap; }
  .company__name { font-weight: 700; }
  .company .contact-list { margin-top: 22px; }
</style>
</head>
<body>

  <section class="card card--front" aria-label="Visitenkarte Vorderseite">
    <div class="wordmark"><span class="wordmark__dot"></span>Vertriebsbrücke</div>
  </section>

  <section class="card card--back" aria-label="Visitenkarte Rückseite">
    <div class="bar bar--top-right"></div>
    <div class="bar bar--personal"></div>
    <div class="bar bar--bottom"></div>

    <div class="person">
      <div class="person__heading">
        <span class="person__name">Jonas Reinhardt</span>
        <span class="person__role">Geschäftsführer / CEO</span>
      </div>
      <ul class="contact-list">
        <li><span class="icon"><svg viewBox="0 0 10 10"><path d="M2 1l2 2-1 1.2c.6 1.2 1.6 2.2 2.8 2.8L7 6l2 2-1.3 1.3C4.5 9 1 5.5.7 2.3z" fill="#fff"/></svg></span>+49 6100 / 11 22 33 44</li>
        <li><span class="icon"><svg viewBox="0 0 10 10"><rect x="1" y="2.5" width="8" height="5" fill="none" stroke="#fff" stroke-width="1"/><path d="M1 2.5l4 3 4-3" fill="none" stroke="#fff" stroke-width="1"/></svg></span>jr@vertriebsbruecke-online.de</li>
      </ul>
    </div>

    <div class="portrait" role="img" aria-label="Porträtfoto des Geschäftsführers"></div>

    <div class="wordmark"><span class="wordmark__dot"></span>Vertriebsbrücke</div>

    <div class="company">
      <p class="company__address"><span class="company__name">JRB Vertriebsbrücke GmbH i.G.</span> • Lindenweg 4</p>
      <p class="company__address">64283 Musterstadt</p>
      <ul class="contact-list">
        <li><span class="icon"><svg viewBox="0 0 10 10"><path d="M2 1l2 2-1 1.2c.6 1.2 1.6 2.2 2.8 2.8L7 6l2 2-1.3 1.3C4.5 9 1 5.5.7 2.3z" fill="#fff"/></svg></span>+49 6100 / 11 22 33 44</li>
        <li><span class="icon"><svg viewBox="0 0 10 10"><rect x="1" y="2.5" width="8" height="5" fill="none" stroke="#fff" stroke-width="1"/><path d="M1 2.5l4 3 4-3" fill="none" stroke="#fff" stroke-width="1"/></svg></span>info@vertriebsbruecke-online.de</li>
        <li><span class="icon"><svg viewBox="0 0 10 10"><circle cx="5" cy="5" r="4" fill="none" stroke="#fff" stroke-width="1"/><path d="M1 5h8M5 1c-2 2.5-2 5.5 0 8M5 1c2 2.5 2 5.5 0 8" fill="none" stroke="#fff" stroke-width=".8"/></svg></span>www.vertriebsbruecke-online.de</li>
      </ul>
    </div>
  </section>

</body>
</html>
```